Residential Remodeling Contractor needs updated business card

I need a new design for my business card.
Name of the company is Ridgefell Construction. I need a card that commands presence, strength, integrity. I have been in business for 28 years. I am a Residential Remodeling Contractor that covers all aspects of a residential remodel and build.

```html
<!DOCTYPE html>
<html lang="en">
<head>
<meta charset="utf-8">
<title>Ridgefell Construction – Business Card</title>
<link rel="stylesheet" href="https://fonts.googleapis.com/css2?family=Montserrat:wght@400;600&display=swap">
<style>
  :root {
    --backdrop: #232323;
    --card-blue: #233f80;
    --white: #ffffff;
    --soft-white: rgba(255,255,255,0.85);
    --glow: rgba(190,200,235,0.55);
  }
  * { box-sizing: border-box; margin: 0; padding: 0; }
  html, body { width: 1200px; height: 900px; overflow: hidden; }
  body {
    background: var(--backdrop);
    font-family: "Montserrat", Arial, sans-serif;
    color: var(--white);
    position: relative;
  }
  .card {
    position: absolute;
    left: 250px;
    width: 700px;
    height: 400px;
    background: var(--card-blue);
    overflow: hidden;
    box-shadow: 0 10px 30px rgba(0,0,0,0.5);
  }
  .card::after {
    content: "";
    position: absolute;
    left: 0; right: 0; bottom: 0;
    height: 14px;
    background: var(--white);
  }
  .card--front { top: 40px; }
  .card--back { top: 470px; }

  .wordmark {
    position: absolute;
    display: flex;
    align-items: center;
    gap: 18px;
  }
  .wordmark__square {
    background: var(--white);
    flex: none;
  }
  .wordmark__name {
    font-family: "Montserrat", Arial, sans-serif;
    font-weight: 600;
    color: var(--white);
    line-height: 1.15;
    text-transform: uppercase;
    letter-spacing: 2px;
  }
  .wordmark__name span { display: block; }

  .card--front .wordmark { left: 170px; top: 150px; }
  .card--front .wordmark__square { width: 30px; height: 30px; }
  .card--front .wordmark__name { font-size: 38px; }

  .card--back .wordmark { left: 50px; top: 110px; }
  .card--back .wordmark__square { width: 24px; height: 24px; }
  .card--back .wordmark__name { font-size: 30px; }

  .accent-glow {
    position: absolute;
    right: 0; top: 120px;
    width: 300px; height: 210px;
    background: linear-gradient(100deg, rgba(190,200,235,0) 0%, rgba(190,200,235,0.18) 55%, var(--glow) 100%);
  }

  .person {
    position: absolute;
    right: 44px;
    top: 32px;
    text-align: right;
  }
  .person__name { font-size: 26px; font-weight: 600; line-height: 1.2; }
  .person__role { font-size: 14px; font-weight: 400; color: var(--soft-white); }
  .person-bar {
    position: absolute;
    right: 0; top: 28px;
    width: 16px; height: 46px;
    background: var(--white);
  }

  .contact {
    position: absolute;
    left: 50px;
    bottom: 40px;
    font-size: 15px;
    line-height: 1.3;
  }
  .contact__address { margin-bottom: 18px; }
  .contact__list { list-style: none; }
  .contact__list li {
    display: flex; align-items: center; gap: 12px;
    margin-top: 9px;
  }
  .contact__list svg { width: 16px; height: 16px; fill: var(--white); flex: none; }
</style>
</head>
<body>

<section class="card card--front" aria-label="Card front">
  <div class="wordmark">
    <div class="wordmark__square"></div>
    <div class="wordmark__name"><span>Ridgefell</span><span>Construction</span></div>
  </div>
</section>

<section class="card card--back" aria-label="Card back">
  <div class="accent-glow" role="img" aria-label="Faint light accent decoration"></div>

  <div class="person">
    <div class="person__name">Daniel Hart</div>
    <div class="person__role">Owner</div>
  </div>
  <div class="person-bar"></div>

  <div class="wordmark">
    <div class="wordmark__square"></div>
    <div class="wordmark__name"><span>Ridgefell</span><span>Construction</span></div>
  </div>

  <div class="contact">
    <p class="contact__address">24 Cedar Hollow Road<br>Brandon, MS 39042</p>
    <ul class="contact__list">
      <li>
        <svg viewBox="0 0 16 16" aria-hidden="true"><path d="M1 5c0-2 3-3 7-3s7 1 7 3v1h-3V5H4v1H1zM3 7h10l1 7H2zm5 1.5a2.5 2.5 0 1 0 0 5 2.5 2.5 0 0 0 0-5z"/></svg>
        555.014.2287
      </li>
      <li>
        <svg viewBox="0 0 16 16" aria-hidden="true"><path d="M1 3h14v10H1zm1.5 1.2V5l5.5 4 5.5-4v-.8z"/></svg>
        info@ridgefellconstruction.com
      </li>
      <li>
        <svg viewBox="0 0 16 16" aria-hidden="true"><circle cx="8" cy="8" r="7"/><path d="M1 8h14M8 1c-3 3-3 11 0 14M8 1c3 3 3 11 0 14" stroke="#233f80" stroke-width="1" fill="none"/></svg>
        www.ridgefellconstruction.com
      </li>
    </ul>
  </div>
</section>

</body>
</html>
```